Professional Services - letterhead / business cards

The company (velmora partners) will provide services to Investment Funds and large investors in Spain. I have recently chosen a logo that I am attaching.

I would like a simple stationary design that i could use as letter head, business cards and "with compliments" cards.

I am not quite sure which color I will mostly use for the logo, in the email signature I will probably lean towards the white background and grey letters. I am attaching my favourite options.

Target Market(s)

Large Multinationals, Investment funds and Law firms

Industry/Entity Type

Business

Requirements
Must have
• my details are:
Luis R. Abadal
Velmora Partners S.L.
Casa de Torrelumbre
Calle de Vientoalto 27
28014 Madrid
T: +34 (91) 387-2265
M: +34 (646) 819-054
e-mail: labadal@velmorapartners.com

```html
<!DOCTYPE html>
<html lang="en">
<head>
<meta charset="utf-8">
<title>Velmora Partners – Stationery</title>
<link rel="stylesheet" href="https://fonts.googleapis.com/css2?family=Quicksand:wght@400&family=PT+Sans:wght@400;700&family=Kaushan+Script&display=swap">
<style>
:root{
  --navy:#2b2a6d;
  --paper:#ffffff;
  --paper-shade:#ececf0;
  --grey:#8a8a92;
  --ink-soft:#d6d6de;
  --stage:#8e5a36;
  --label:#ffffff;
}
*{box-sizing:border-box;margin:0;padding:0}
html,body{width:1200px;height:373px;overflow:hidden}
body{background:var(--stage);position:relative;font-family:"PT Sans",sans-serif}
.piece{position:absolute;background:linear-gradient(160deg,var(--paper) 55%,var(--paper-shade));box-shadow:0 1px 3px rgba(0,0,0,.35);overflow:hidden}
.brand{font-family:"Quicksand",sans-serif;font-weight:400;color:var(--navy);white-space:nowrap;position:absolute;letter-spacing:.2px}
.small{font-size:5px;line-height:7px;color:var(--grey);position:absolute}
.label{position:absolute;color:var(--label);font-size:20px;transform:translateX(-50%)}
.band{position:absolute;left:0;right:0;background:var(--navy);color:#fff}

/* letterhead option 1 */
.lh1{left:3px;top:4px;width:258px;height:334px}
.lh1 .brand{left:10px;top:10px;font-size:15px}
.lh1 .address{right:14px;top:10px;padding-left:4px;border-left:1px solid var(--ink-soft)}
.lh1 .watermark{position:absolute;left:36px;top:160px;font-family:"Quicksand",sans-serif;font-size:34px;color:var(--ink-soft);transform:rotate(-27deg);white-space:nowrap}
.lh1 .phone{position:absolute;bottom:6px;width:100%;text-align:center;font-size:7px;color:var(--grey)}

/* letterhead option 2 */
.lh2{left:286px;top:4px;width:259px;height:334px}
.lh2 .brand{left:0;right:0;text-align:center;top:11px;font-size:15px}
.lh2 .band{bottom:0;height:13px;font-size:5px;line-height:13px;text-align:center}

/* envelopes */
.env-back{left:631px;top:4px;width:289px;height:130px}
.env-back svg,.env-mid svg{position:absolute;left:0;top:0}
.env-back .brand{left:0;right:0;text-align:center;top:20px;font-size:14px;color:#fff}
.env-mid{left:568px;top:61px;width:289px;height:128px}
.env-mid .brand{left:0;right:0;text-align:center;top:16px;font-size:16px}
.env-front{left:599px;top:118px;width:289px;height:129px}
.env-front .brand{left:9px;top:12px;font-size:14px}
.env-front .address{left:9px;top:32px}
.env-front .band{bottom:0;height:5px}

/* compliments slip */
.slip{left:945px;top:119px;width:252px;height:118px}
.slip .brand{left:0;right:0;text-align:center;top:14px;font-size:18px}
.slip .greeting{position:absolute;left:0;right:0;top:56px;text-align:center;font-family:"Kaushan Script",cursive;color:var(--navy);font-size:13px}
.slip .band{bottom:0;height:36px}

/* contact block used on slip and card */
.contact{position:absolute;display:flex;font-size:4.6px;line-height:7.5px;color:#fff}
.contact .addr{text-align:right;padding-right:5px;border-right:1px solid rgba(255,255,255,.6)}
.contact .lines{padding-left:5px}
.slip .contact{left:70px;top:6px}

/* business cards */
.card{top:268px;width:129px;height:73px}
.card-front{left:574px}
.card-front .brand{left:8px;top:10px;font-size:11px}
.card-front .person{position:absolute;left:0;right:0;top:31px;text-align:center;font-size:5.5px;font-weight:700;color:var(--navy)}
.card-front .person span{font-weight:400;color:var(--grey);font-size:4px}
.card-front .band{bottom:0;height:31px}
.card-front .contact{left:18px;top:3px;font-size:3.6px;line-height:6px}
.card-white{left:709px}
.card-navy{left:844px;background:var(--navy)}
.card-white .brand,.card-navy .brand{left:0;right:0;text-align:center;top:29px;font-size:11px}
.card-navy .brand{color:#fff}
.icon{display:inline-block;width:4px;height:4px;vertical-align:middle;margin-right:2px}
</style>
</head>
<body>

<section class="piece lh1" aria-label="Letterhead option 1">
  <div class="brand">velmora partners</div>
  <div class="small address">Casa de Torrelumbre<br>Calle de Vientoalto 27<br>28014 Madrid</div>
  <div class="watermark" aria-hidden="true">velmora partners</div>
  <div class="phone">&#9990; +34 (91) 387-2265</div>
</section>

<section class="piece lh2" aria-label="Letterhead option 2">
  <div class="brand">velmora partners</div>
  <div class="band">Casa de Torrelumbre, Calle de Vientoalto 27, 28014 Madrid &nbsp;|&nbsp; &#9990; +34 (91) 387-2265</div>
</section>

<section class="piece env-back" aria-label="Envelope back">
  <svg width="289" height="130" viewBox="0 0 289 130" aria-hidden="true">
    <path d="M0 0 H289 V8 Q285 20 265 24 L165 48 Q144 54 123 48 L24 24 Q4 20 0 8 Z" fill="var(--navy)"/>
  </svg>
  <div class="brand">velmora partners</div>
</section>

<section class="piece env-mid" aria-label="Envelope flap">
  <svg width="289" height="128" viewBox="0 0 289 128" aria-hidden="true">
    <path d="M0 2 Q2 14 20 18 L125 50 Q144 56 163 50 L268 18 Q286 14 289 2" fill="none" stroke="#555" stroke-width="0.8"/>
  </svg>
  <div class="brand">velmora partners</div>
</section>

<section class="piece env-front" aria-label="Envelope front">
  <div class="brand">velmora partners</div>
  <div class="small address">Casa de Torrelumbre, Calle de Vientoalto 27, 28014 Madrid</div>
  <div class="band"></div>
</section>

<section class="piece slip" aria-label="With compliments slip">
  <div class="brand">velmora partners</div>
  <div class="greeting">With Compliments</div>
  <div class="band">
    <div class="contact">
      <div class="addr">Casa de Torrelumbre<br>Calle de Vientoalto 27<br>28014 Madrid</div>
      <div class="lines">&#9990; +34 (91) 387-2265<br>&#9743; +34 (646) 819-054<br>&#9993; labadal@velmorapartners.com</div>
    </div>
  </div>
</section>

<section class="piece card card-front" aria-label="Business card front">
  <div class="brand">velmora partners</div>
  <div class="person">Luis R. Abadal, <span>Velmora Partners S.L.</span></div>
  <div class="band">
    <div class="contact">
      <div class="addr">Casa de Torrelumbre<br>Calle de Vientoalto 27<br>28014 Madrid</div>
      <div class="lines">&#9990; +34 (91) 387-2265<br>&#9743; +34 (646) 819-054<br>&#9993; labadal@velmorapartners.com</div>
    </div>
  </div>
</section>

<section class="piece card card-white" aria-label="Business card back, white">
  <div class="brand">velmora partners</div>
</section>

<section class="piece card card-navy" aria-label="Business card back, navy">
  <div class="brand">velmora partners</div>
</section>

<div class="label" style="left:125px;top:344px">Option-1</div>
<div class="label" style="left:408px;top:344px">Option-2</div>
<div class="label" style="left:1063px;top:242px;font-size:16px">Compliments</div>

</body>
</html>
```